Coastline Premier Retreats Business Card Design

Design a business card for Coastline Premier Retreats. Look at the website for colors and reference. Card should have logo, name, title, office number, mobile number, email, URL and a tagline like, "Luxury Hotel & Resort Email Marketing" (This might change).

https://www.coastlinepremierretreats.example

The rest I will leave up to your imagination.

Contact Information for Business Card

Logo, name, title, office number, mobile number, email, URL and a tagline like, "Luxury Hotel & Resort Email Marketing" (This might change).

```html
<!DOCTYPE html>
<html lang="en">
<head>
<meta charset="utf-8">
<title>Coastline Premier Retreats — Business Card</title>
<link rel="stylesheet" href="https://fonts.googleapis.com/css2?family=Open+Sans:wght@400;600;700;800&display=swap">
<style>
  :root {
    --backdrop: #232323;
    --card: #1f1f22;
    --card-edge: #f06a1c;
    --accent: #f26b1d;
    --ink-light: #ffffff;
    --ink-muted: #e9e9e9;
    --deboss: #151517;
  }
  * { box-sizing: border-box; margin: 0; padding: 0; }
  html, body { width: 1200px; height: 780px; overflow: hidden; }
  body {
    background: var(--backdrop);
    font-family: "Open Sans", Arial, sans-serif;
    position: relative;
  }
  .card {
    position: absolute;
    top: 90px;
    width: 343px;
    height: 600px;
    background: var(--card);
    border: 2px solid var(--card-edge);
    border-radius: 24px;
    overflow: hidden;
    box-shadow: 0 18px 40px rgba(0,0,0,0.55);
  }
  .card--back { left: 235px; }
  .card--front { left: 622px; }

  /* Back: debossed name set vertically */
  .back-mark {
    position: absolute;
    left: 50%;
    top: 50%;
    width: 520px;
    transform: translate(-50%, -50%) rotate(-90deg);
    display: flex;
    align-items: center;
    justify-content: center;
    gap: 16px;
    color: var(--deboss);
    font-weight: 800;
    font-size: 40px;
    letter-spacing: 1px;
    text-transform: uppercase;
    line-height: 1.05;
  }
  .back-mark__square {
    width: 34px; height: 34px;
    background: var(--deboss);
    flex: none;
  }

  /* Front */
  .brand {
    position: absolute;
    top: 48px;
    left: 28px;
    right: 28px;
    display: flex;
    align-items: center;
    justify-content: center;
    gap: 9px;
    color: var(--ink-light);
    font-weight: 800;
    font-size: 14px;
    letter-spacing: 0.3px;
    text-transform: uppercase;
    white-space: nowrap;
  }
  .brand__square {
    width: 13px; height: 13px;
    background: var(--accent);
    flex: none;
  }
  .person {
    position: absolute;
    left: 34px;
    right: 24px;
    top: 330px;
  }
  .person__name {
    font-size: 28px;
    font-weight: 800;
    line-height: 1.1;
    color: var(--ink-light);
  }
  .person__name .given { color: var(--accent); }
  .person__title {
    margin-top: 4px;
    font-size: 15px;
    font-weight: 600;
    color: var(--ink-light);
  }
  .tagline {
    margin-top: 14px;
    font-size: 14px;
    color: var(--accent);
    line-height: 1.3;
  }
  .contacts {
    list-style: none;
    margin-top: 18px;
  }
  .contacts li {
    display: flex;
    align-items: center;
    gap: 10px;
    font-size: 13px;
    color: var(--ink-muted);
    line-height: 1;
    margin-bottom: 9px;
    white-space: nowrap;
  }
  .contacts svg { width: 14px; height: 14px; flex: none; }
</style>
</head>
<body>

  <section class="card card--back" aria-label="Card back">
    <div class="back-mark">
      <span class="back-mark__square"></span>
      <span>Coastline<br>Premier Retreats</span>
    </div>
  </section>

  <section class="card card--front" aria-label="Card front">
    <div class="brand">
      <span class="brand__square"></span>
      <span>Coastline Premier Retreats</span>
    </div>

    <div class="person">
      <h1 class="person__name"><span class="given">Lena</span> Havlikova</h1>
      <p class="person__title">Co-Founder</p>
      <p class="tagline">Luxury Hotel &amp;<br>Resort Email Marketing</p>

      <ul class="contacts">
        <li>
          <svg viewBox="0 0 24 24" aria-hidden="true"><path fill="#f26b1d" d="M6.6 10.8a15 15 0 0 0 6.6 6.6l2.2-2.2a1 1 0 0 1 1-.25 11.4 11.4 0 0 0 3.6.57 1 1 0 0 1 1 1V20a1 1 0 0 1-1 1A17 17 0 0 1 3 4a1 1 0 0 1 1-1h3.5a1 1 0 0 1 1 1c0 1.25.2 2.46.57 3.6a1 1 0 0 1-.25 1z"/></svg>
          (555) 214-3086
        </li>
        <li>
          <svg viewBox="0 0 24 24" aria-hidden="true"><rect x="6" y="2" width="12" height="20" rx="2" fill="none" stroke="#f26b1d" stroke-width="2"/><circle cx="12" cy="18" r="1.2" fill="#f26b1d"/></svg>
          (555) 610-4492
        </li>
        <li>
          <svg viewBox="0 0 24 24" aria-hidden="true"><circle cx="12" cy="12" r="9" fill="none" stroke="#f26b1d" stroke-width="2"/><path d="M3 12h18M12 3c3 3 3 15 0 18M12 3c-3 3-3 15 0 18" fill="none" stroke="#f26b1d" stroke-width="1.6"/></svg>
          www.coastlinepremierretreats.example
        </li>
        <li>
          <svg viewBox="0 0 24 24" aria-hidden="true"><rect x="2" y="5" width="20" height="14" rx="2" fill="none" stroke="#f26b1d" stroke-width="2"/><path d="M3 6l9 7 9-7" fill="none" stroke="#f26b1d" stroke-width="2"/></svg>
          info@coastlinepremierretreats.example
        </li>
      </ul>
    </div>
  </section>

</body>
</html>
```